Business card design needed

I would like a one sided black business card with the information provided above. Refer to my website www.brightvolleyracquets.com.au for an example of colors I have used for my site, would like to keep this consistent for my business cards also, I will upload my logo below.

I am a new small business that provides tennis customers with racquet re stringing, tennis strings and accessories.

Industry/Entity Type

Small Business

Contact Information for Business Card

Bright Volley Tennis

Owen Whitby
Managing Director

brightvolleyracquets@mailbox.example
www.brightvolleyracquets.com.au
0491 726 305

Racquet Restringing/Tennis Strings/Accessories

Requirements
Must have
• Must have my logo and card must be black

```html
<!DOCTYPE html>
<html lang="en">
<head>
<meta charset="utf-8">
<title>Bright Volley Tennis – Business Card</title>
<link href="https://fonts.googleapis.com/css2?family=Arimo:wght@400;700&display=swap" rel="stylesheet">
<style>
  :root {
    --stage: #e4e1dc;
    --card: #000000;
    --lime: #b5d334;
    --rule: #3a3a3a;
    --ink: #ffffff;
    --ink-dark: #111111;
  }
  * { margin: 0; padding: 0; box-sizing: border-box; }
  html, body {
    width: 1200px;
    height: 475px;
    overflow: hidden;
    background: var(--stage);
    font-family: "Arimo", Arial, sans-serif;
  }
  .canvas {
    position: relative;
    width: 1200px;
    height: 475px;
  }
  .card {
    position: absolute;
    background: var(--card);
    color: var(--ink);
  }
  .card--front {
    left: 35px; top: 81px;
    width: 545px; height: 312px;
    border-radius: 6px 16px 6px 16px;
  }
  .card--back {
    left: 607px; top: 86px;
    width: 547px; height: 313px;
    border-radius: 6px 28px 6px 28px;
  }
  .brand {
    position: absolute;
    left: 0; right: 0;
    display: flex;
    align-items: center;
    justify-content: center;
    gap: 12px;
  }
  .card--front .brand { top: 72px; }
  .card--back .brand { top: 108px; }
  .brand__dot {
    width: 30px; height: 30px;
    border-radius: 50%;
    background: var(--lime);
  }
  .brand__name {
    font-weight: 700;
    font-size: 34px;
    color: var(--lime);
    letter-spacing: 0.5px;
    text-transform: uppercase;
  }
  .title-band {
    position: absolute;
    left: 0; right: 0;
    top: 180px;
    height: 34px;
    background: var(--lime);
    color: var(--ink-dark);
    display: flex;
    align-items: center;
    justify-content: center;
    gap: 6px;
    box-shadow: 0 -4px 0 -1px var(--card), 0 -5px 0 0 var(--rule),
                0 4px 0 -1px var(--card), 0 5px 0 0 var(--rule);
  }
  .title-band__name { font-size: 17px; text-transform: uppercase; }
  .title-band__role { font-size: 14px; }
  .contact {
    position: absolute;
    left: 0; right: 0;
    top: 225px;
    list-style: none;
    text-align: center;
    font-size: 14px;
    line-height: 18px;
    letter-spacing: 0.3px;
  }
  .website {
    position: absolute;
    left: 0; right: 0;
    top: 237px;
    text-align: center;
    font-size: 13.5px;
    letter-spacing: 1.6px;
  }
</style>
</head>
<body>
<main class="canvas">
  <section class="card card--front" aria-label="Business card front">
    <div class="brand">
      <span class="brand__dot"></span>
      <span class="brand__name">Bright Volley Tennis</span>
    </div>
    <div class="title-band">
      <span class="title-band__name">Owen Whitby,</span>
      <span class="title-band__role">Managing Director</span>
    </div>
    <ul class="contact">
      <li>P : 0491 726 305</li>
      <li>E : brightvolleyracquets@mailbox.example</li>
      <li>W: www.brightvolleyracquets.com.au</li>
    </ul>
  </section>

  <section class="card card--back" aria-label="Business card back">
    <div class="brand">
      <span class="brand__dot"></span>
      <span class="brand__name">Bright Volley Tennis</span>
    </div>
    <p class="website">www.brightvolleyracquets.com.au</p>
  </section>
</main>
</body>
</html>
```